2021 Summer Ads Hollis Bay Custom Homes

We need a re-design of our summer ad run for our customer, Hollis Bay Custom Homes. They are custom home builders in the mostly rural parts of West Virginia, USA. They are known for their "Forever Home" tagline. We'd like two designed ads with the main difference being just the custom home that's featured. These designs should be for a Zintrola banner like 300 x 250 and square ad like 250 x 250. For inspiration please visit the Hollis Bay Custom Homes website at www dot hollisbaycustomhomes dot com

Target Market(s)

consumers / new home shoppers

Industry/Entity Type

Consumer

Requirements
Must have
• HBCH logo
Price Lock Available!
Custom home pic
Learn more >
small CFRM logo mark

```html
<!DOCTYPE html>
<html lang="en">
<head>
<meta charset="utf-8">
<title>Hollis Bay Custom Homes – Summer Ad</title>
<link rel="stylesheet" href="https://fonts.googleapis.com/css2?family=Montserrat:wght@400;600;800&display=swap">
<style>
  :root {
    --ink: #1d1f27;
    --ink-soft: #262a33;
    --brand-red: #d9182b;
    --brand-red-deep: #9e0f1c;
    --paper: #ffffff;
    --sky: #c9d8e6;
    --siding: #8d97a6;
    --roof: #4a4f58;
  }
  html, body {
    margin: 0;
    padding: 0;
    width: 1200px;
    height: 1000px;
    overflow: hidden;
    background: var(--ink);
  }
  .ad {
    position: relative;
    width: 1200px;
    height: 1000px;
    overflow: hidden;
    background: var(--ink);
    font-family: "Montserrat", Arial, sans-serif;
    color: var(--paper);
  }
  .ad__home-photo {
    position: absolute;
    inset: 0;
    clip-path: polygon(600px 0, 1200px 0, 1200px 1000px, 640px 1000px);
    background:
      linear-gradient(180deg, var(--sky) 0%, #aebfd0 18%, var(--roof) 30%, var(--siding) 45%, #a3acb8 62%, #7b8390 80%, #9aa1ab 100%);
  }
  .ad__shapes {
    position: absolute;
    inset: 0;
  }
  .ad__brand {
    position: absolute;
    left: 60px;
    top: 220px;
    width: 380px;
    text-align: center;
    font-weight: 600;
    color: var(--paper);
    text-transform: uppercase;
    line-height: 1.15;
  }
  .ad__brand-name {
    display: block;
    font-size: 48px;
    letter-spacing: 2px;
  }
  .ad__brand-sub {
    display: block;
    font-size: 22px;
    letter-spacing: 6px;
    margin-top: 10px;
  }
  .ad__headline {
    position: absolute;
    left: 60px;
    top: 436px;
    margin: 0;
    font-size: 62px;
    line-height: 70px;
    text-transform: uppercase;
    letter-spacing: 0;
    white-space: nowrap;
  }
  .ad__headline-light { display: block; font-weight: 400; }
  .ad__headline-bold { display: block; font-weight: 800; }
  .ad__offer {
    position: absolute;
    left: 64px;
    top: 744px;
    margin: 0;
    font-size: 26px;
    line-height: 32px;
    font-weight: 800;
    letter-spacing: 0.5px;
  }
  .ad__cta {
    position: absolute;
    left: 62px;
    top: 820px;
    width: 340px;
    height: 96px;
    border-radius: 6px;
    background: var(--brand-red);
    color: var(--paper);
    font-size: 28px;
    font-weight: 800;
    display: flex;
    align-items: center;
    justify-content: center;
    gap: 14px;
    text-decoration: none;
    letter-spacing: 0.5px;
  }
  .ad__cta svg { width: 18px; height: 28px; }
  .ad__partner-badge {
    position: absolute;
    left: 1040px;
    top: 850px;
    width: 120px;
    height: 120px;
    background: var(--paper);
  }
</style>
</head>
<body>
  <main class="ad">
    <div class="ad__home-photo" role="img" aria-label="Rendering of a two-storey grey-sided custom home with a wraparound white-railed deck under a light blue sky"></div>

    <svg class="ad__shapes" viewBox="0 0 1200 1000" width="1200" height="1000" aria-hidden="true">
      <defs>
        <linearGradient id="red-band" x1="0" y1="1" x2="1" y2="0">
          <stop offset="0" stop-color="var(--brand-red-deep)"/>
          <stop offset="0.5" stop-color="var(--brand-red)"/>
          <stop offset="1" stop-color="var(--brand-red)"/>
        </linearGradient>
      </defs>
      <polygon class="shape-top-stripe" points="370,0 600,0 280,150" fill="var(--brand-red)"/>
      <polygon class="shape-edge-stripe" points="608,560 660,520 660,1000 640,1000" fill="var(--brand-red)"/>
      <polygon class="shape-dark-band" points="600,1000 1200,700 1200,745 660,1000" fill="var(--ink-soft)"/>
      <polygon class="shape-red-band" points="660,1000 1200,745 1200,1000" fill="url(#red-band)"/>
    </svg>

    <div class="ad__brand">
      <span class="ad__brand-name">Hollis Bay</span>
      <span class="ad__brand-sub">Custom Homes</span>
    </div>

    <h1 class="ad__headline">
      <span class="ad__headline-light">Start</span>
      <span class="ad__headline-light">Building</span>
      <span class="ad__headline-bold">Your Forever</span>
      <span class="ad__headline-bold">Home Today!</span>
    </h1>

    <p class="ad__offer">PRICE LOCK AVAILABLE!</p>

    <a class="ad__cta" href="#">LEARN MORE
      <svg viewBox="0 0 18 28" aria-hidden="true"><polyline points="3,3 14,14 3,25" fill="none" stroke="currentColor" stroke-width="5"/></svg>
    </a>

    <div class="ad__partner-badge" role="img" aria-label="CFRM partner badge"></div>
  </main>
</body>
</html>
```